Kelvara Pane Works Business Card

We need a business card design that is suitable for a Glazing Business. We Specialize in Repairing broken windows and doors and are a 24hr on call service. We manufacture Shower screens, Fly screens, Wardrobe doors, Security doors and grilles + mirrors. We stock a variety of mesh including Standard mesh, Pet resistant mesh, Tressmet & Clearweft. We would like to use a combination of Light Blue, Dark Blue, Black & White with perhaps a picture of glass breaking.

Industry/Entity Type

Business

Contact Information for Business Card

Narooma Glass Service60B Glasshouse Rocks RdNarooma NSW 2546PH / FAX - 02 44765210MOB - 0419682350 Andrewemail - kelvarapane@fenmail.example

Font styles to use
Serif

Colors
34a7d8
0255a3
ffffff

Requirements
Must have
• logo with picture of broken or cracked glass

```html
<!DOCTYPE html>
<html lang="en">
<head>
<meta charset="utf-8">
<title>Kelvara Pane Works – Business Card</title>
<link rel="stylesheet" href="https://fonts.googleapis.com/css2?family=Questrial&family=Didact+Gothic&family=PT+Sans&display=swap">
<style>
  :root {
    --stage-top: #474747;
    --stage-bottom: #5f5f5f;
    --card-white: #ffffff;
    --sky-blue: #77acdc;
    --sky-blue-light: #8dbbe4;
    --charcoal: #3a3a3a;
    --ink: #000000;
    --text-light: #ffffff;
  }
  * { box-sizing: border-box; margin: 0; padding: 0; }
  html, body { width: 1200px; height: 900px; overflow: hidden; }
  body {
    position: relative;
    background: linear-gradient(to bottom, var(--stage-top), var(--stage-bottom));
    font-family: "PT Sans", sans-serif;
  }

  .card { position: absolute; top: 170px; width: 347px; height: 561px; }

  /* Front */
  .card-front { left: 259px; background: var(--card-white); }
  .name-band {
    position: absolute; left: 12px; top: 9px; width: 323px; height: 67px;
    background: var(--sky-blue);
    display: flex; align-items: center; justify-content: center;
    color: var(--text-light);
    font-family: "Didact Gothic", sans-serif;
    font-size: 25px; letter-spacing: 0.5px;
  }
  .brand-mark {
    position: absolute; left: 106px; top: 101px; width: 108px; height: 108px;
    border-radius: 50%;
    background: var(--sky-blue);
    border: 6px solid var(--charcoal);
  }
  .brand-name {
    position: absolute; left: 0; top: 214px; width: 347px;
    text-align: center;
    color: var(--sky-blue);
    font-family: "Questrial", sans-serif;
    font-size: 33px; line-height: 37px; letter-spacing: 1.5px;
  }
  .contact-panel {
    position: absolute; left: 9px; top: 293px; width: 326px; height: 195px;
    background: var(--ink);
    padding: 59px 0 0 33px;
    list-style: none;
  }
  .contact-item {
    display: flex; align-items: center; gap: 8px;
    height: 28px; margin-bottom: 10px;
    color: var(--text-light); font-size: 15px;
  }
  .contact-icon { width: 28px; height: 28px; flex: none; }
  .address-band {
    position: absolute; left: 9px; top: 490px; width: 326px; height: 56px;
    background: var(--sky-blue);
    display: flex; align-items: center; justify-content: center;
    color: var(--text-light); font-size: 11.5px;
  }

  /* Back */
  .card-back { left: 631px; background: var(--sky-blue); }
  .back-frame {
    position: absolute; left: 30px; top: 27px; width: 287px; height: 501px;
    border: 1px solid var(--text-light);
  }
  .back-emblem {
    position: absolute; left: 70px; top: 164px; width: 206px; height: 206px;
    border-radius: 50%;
    border: 8px solid var(--sky-blue-light);
  }
</style>
</head>
<body>
  <section class="card card-front" aria-label="Business card front">
    <div class="name-band">DORIAN PELL</div>
    <div class="brand-mark" aria-hidden="true"></div>
    <h1 class="brand-name">KELVARA<br>PANE WORKS</h1>
    <ul class="contact-panel">
      <li class="contact-item">
        <svg class="contact-icon" viewBox="0 0 28 28" aria-hidden="true">
          <circle cx="14" cy="14" r="13" fill="var(--sky-blue)" stroke="#fff" stroke-width="1.2"/>
          <path d="M10 8.5c.6-.5 1.3-.4 1.6.2l1.1 2c.3.6.1 1.1-.4 1.5l-.7.5c.6 1.5 1.6 2.6 3.1 3.3l.6-.7c.4-.5 1-.6 1.5-.3l1.9 1.2c.6.4.6 1.1.1 1.6l-.9.9c-.7.7-1.8.8-2.8.3-2.8-1.4-4.8-3.5-6-6.3-.4-1-.3-2 .4-2.7z" fill="#fff"/>
        </svg>
        <span>0419682350</span>
      </li>
      <li class="contact-item">
        <svg class="contact-icon" viewBox="0 0 28 28" aria-hidden="true">
          <circle cx="14" cy="14" r="13" fill="var(--sky-blue)" stroke="#fff" stroke-width="1.2"/>
          <rect x="9" y="11" width="10" height="8" rx="1" fill="#fff"/>
          <rect x="11" y="8" width="6" height="4" fill="#fff"/>
          <rect x="11.5" y="14" width="5" height="3" fill="var(--sky-blue)"/>
        </svg>
        <span>02 48931067</span>
      </li>
      <li class="contact-item">
        <svg class="contact-icon" viewBox="0 0 28 28" aria-hidden="true">
          <circle cx="14" cy="14" r="13" fill="var(--sky-blue)" stroke="#fff" stroke-width="1.2"/>
          <rect x="8" y="10" width="12" height="8.5" rx="1" fill="#fff"/>
          <path d="M8.5 10.5l5.5 4.3 5.5-4.3" fill="none" stroke="var(--sky-blue)" stroke-width="1.2"/>
        </svg>
        <span>kelvarapane@fenmail.example</span>
      </li>
    </ul>
    <div class="address-band">17C Tindale Ridge Rd Brenmoor NSW 2583</div>
  </section>

  <section class="card card-back" aria-label="Business card back">
    <div class="back-frame"></div>
    <div class="back-emblem" aria-hidden="true"></div>
  </section>
</body>
</html>
```